Form Sculptors Business Card

Professional cosmetic surgery company, based in very exclusive area in London. High profiled clientele. Brand is very artistic, modern, state-of-the-art, safe. The best in the business. Celebrity clientele.

Form Sculptor’s of London is a brand serving a discriminating and exclusive clientele who value personal service that is both intimate and high end. Our clients choose Form Sculptors because of the relationships we share with all of our customers. The clients of Form Sculptors have an equal partnership between customers, and very experienced, highly qualified medical professionals. This together provides you with a professional service that keeps you looking good and feeling good. It is a relationship based on honesty, compassion, loyalty and respect.
Form Sculptor’s have provided services for internationally recognised celebrities, and other high profiled individuals.

The cards are used for networking at private, exclusive events with VIPs.

Target Market(s)

Professionals
Rich people

Industry/Entity Type

Professional Service

Contact Information for Business Card

Need double sided business card design for 4 people. Back of the business card needs to have contrast background to the front with butterfly watermark with services provided:
Hair Restoration surgery
Hair Loss treatments
Breast surgery
Rhinoplasty
Pulvix Liposuction
Fat Grafting
Lumaxin & Fillers

Front of the business card needs to be a nice satin black.
with following information:
Calvert Osterlund - name
Chief Executive - Job title

www.formsculptors-example.co.uk
calvert@formsculptors-example.co.uk
Phone: +44 (0)207 946 0321
Mobile: +44 (0)7700 900 147

The London Farrowmere Clinic
14 Farrowmere Lane | London | W1X 4QP
Off Quenby Street

All business cards have the same address, phone, website as Calvert's details.
Same details on the back of the business card as well.
The other cards have different name, job title, email, mobile number

Teodor Lunn - Name
Partner - Job Title
Former England International Cricketer - please include below job title

email: teodor@formsculptors-example.co.uk
mobile: +44(0)7700 900582

Dr Castello Vranesk - Name
Plastic Surgeon - Job Title
drvranesk@formsculptors-example.co.uk
No mobile number

Dr Ezra Tolquist FRCS (please put FRCS in small font) - Name
Hair Restoration Surgeon - Job Title
drtolquist@formsculptors-example.co.uk
No mobile number

Colors
cedeec
85abd2
0655a3

Requirements
Must have
• The logo needs to be in a metallic finish
• Text needs to be striking
• nice background
• butterfly watermark on the back

```html
<!DOCTYPE html>
<html lang="en">
<head>
<meta charset="utf-8">
<title>Form Sculptors Business Card</title>
<link href="https://fonts.googleapis.com/css2?family=Lato:wght@400;700;900&display=swap" rel="stylesheet">
<style>
  :root {
    --page: #e4e5e7;
    --brand-blue: #1a83c6;
    --deep-blue: #0655a3;
    --satin-black: #333335;
    --card-light: #f1f1f1;
    --card-white: #ffffff;
    --text-dark: #3a3a3c;
    --text-mid: #555558;
    --watermark: #5c5c5f;
    --rule-blue: #85abd2;
  }
  html, body {
    margin: 0;
    padding: 0;
    width: 1000px;
    height: 1200px;
    overflow: hidden;
    background: var(--page);
    font-family: "Lato", sans-serif;
  }
  .card {
    position: absolute;
    left: 70px;
    width: 860px;
    height: 510px;
    overflow: hidden;
    box-shadow: 0 6px 18px rgba(0,0,0,0.18);
  }
  .card-front { top: 50px; background: var(--card-white); }
  .card-back { top: 640px; background: var(--satin-black); }
  .card-shapes { position: absolute; inset: 0; }
  .fill-blue { fill: var(--brand-blue); }
  .fill-dark { fill: var(--satin-black); }
  .fill-light { fill: var(--card-light); }
  .fill-rule { stroke: var(--rule-blue); stroke-width: 1.2; fill: none; }

  .brand-name {
    position: absolute;
    left: 40px;
    top: 246px;
    margin: 0;
    font-weight: 400;
    font-size: 30px;
    letter-spacing: 0.5px;
    color: #e9f6fb;
    white-space: nowrap;
    display: flex;
    align-items: center;
    gap: 10px;
  }
  .brand-dot {
    width: 14px; height: 14px;
    border-radius: 50%;
    background: #cedeec;
  }

  .person {
    position: absolute;
    right: 60px;
    top: 100px;
    text-align: right;
    color: var(--card-white);
  }
  .person-name {
    margin: 0;
    font-size: 24px;
    font-weight: 400;
    text-transform: uppercase;
    letter-spacing: 0.3px;
  }
  .person-name strong { font-weight: 900; }
  .person-title { margin: 4px 0 0; font-size: 14px; }

  .company {
    position: absolute;
    right: 60px;
    top: 246px;
    text-align: right;
  }
  .company-name {
    margin: 0;
    font-size: 23px;
    font-weight: 400;
    color: var(--text-dark);
    text-transform: uppercase;
  }
  .company-name strong { color: var(--brand-blue); font-weight: 900; }
  .company-address { margin: 4px 0 0; font-size: 13px; color: var(--text-mid); }

  .contact-group {
    position: absolute;
    right: 115px;
    text-align: right;
    font-size: 15px;
    line-height: 22px;
    color: var(--text-dark);
  }
  .contact-phone { top: 332px; }
  .contact-web { top: 398px; }
  .contact-group p { margin: 0; }

  .back-watermark {
    position: absolute;
    left: 0; right: 0;
    top: 150px;
    margin: 0;
    text-align: center;
    font-size: 62px;
    font-weight: 400;
    color: var(--watermark);
  }
  .back-band {
    position: absolute;
    left: 0; right: 0; bottom: 0;
    height: 106px;
    background: var(--brand-blue);
    text-align: center;
    color: var(--card-white);
  }
  .back-company {
    margin: 22px 0 0;
    font-size: 27px;
    font-weight: 400;
    text-transform: uppercase;
  }
  .back-company strong { font-weight: 900; }
  .back-web {
    margin: 4px 0 0;
    font-size: 16px;
    font-weight: 700;
    letter-spacing: 1px;
    text-transform: uppercase;
  }
</style>
</head>
<body>

<section class="card card-front" aria-label="Card front">
  <svg class="card-shapes" width="860" height="510" viewBox="0 0 860 510">
    <polygon class="fill-blue" points="0,0 287,0 397,205 296,510 0,510"/>
    <polygon class="fill-dark" points="303,0 860,0 860,198 409,198"/>
    <polygon class="fill-light" points="414,212 860,212 860,510 312,510"/>
    <line class="fill-rule" x1="440" y1="352" x2="790" y2="358"/>
    <line class="fill-rule" x1="440" y1="414" x2="790" y2="420"/>
    <g class="icon-phone" transform="translate(800,357)">
      <polygon class="fill-blue" points="-24,0 -12,-21 12,-21 24,0 12,21 -12,21"/>
      <path d="M-10,-4 q10,-9 20,0 l-3,4 h-3 l-1,-3 h-6 l-1,3 h-3 z M-7,1 h14 l2,8 h-18 z" fill="#fff"/>
    </g>
    <g class="icon-web" transform="translate(800,420)">
      <polygon class="fill-blue" points="-24,0 -12,-21 12,-21 24,0 12,21 -12,21"/>
      <rect x="-11" y="-9" width="22" height="14" rx="1" fill="none" stroke="#fff" stroke-width="2"/>
      <rect x="-6" y="7" width="12" height="2.5" fill="#fff"/>
    </g>
  </svg>

  <h2 class="brand-name"><span class="brand-dot"></span>Form Sculptors</h2>

  <div class="person">
    <h1 class="person-name"><strong>Calvert</strong> Osterlund</h1>
    <p class="person-title">Chief Executive</p>
  </div>

  <div class="company">
    <h3 class="company-name"><strong>Formsculptors</strong> Company</h3>
    <p class="company-address">The London Farrowmere Clinic 14 Farrowmere Lane</p>
  </div>

  <div class="contact-group contact-phone">
    <p>+44 (0)207 946 0321</p>
    <p>+44 (0)7700 900 147</p>
  </div>
  <div class="contact-group contact-web">
    <p>calvert@formsculptors-example.co.uk</p>
    <p>www.formsculptors-example.co.uk</p>
  </div>
</section>

<section class="card card-back" aria-label="Card back">
  <p class="back-watermark">Form Sculptors</p>
  <div class="back-band">
    <h3 class="back-company"><strong>Formsculptors</strong> Company</h3>
    <p class="back-web">www.formsculptors-example.co.uk</p>
  </div>
</section>

</body>
</html>
```